Business Card Design for a Personal Trainer

I need a business card design for my job as a personal trainer. It should have a unique, modern and exclusive design. On the front there should be only my logo with my name and my job. 0162/3819204 Tobias Lendhart Wiesengrundweg 14 80417 Munich Germany The most important contact information is the web adress. it can be bigger than the rest, but its not necessary. The card should be 8,5cmx5,5cm big. Font: Roboto. Colors: black, white, gray, 56c1ff.

```html
<!DOCTYPE html>
<html lang="de">
<head>
<meta charset="utf-8">
<title>Tobias Lendhart – Business Card</title>
<link rel="stylesheet" href="https://fonts.googleapis.com/css2?family=Roboto:wght@400;500&family=Work+Sans:wght@400;500&display=swap">
<style>
  :root {
    --backdrop: #dedede;
    --card-white: #ffffff;
    --card-black: #070809;
    --ink: #1b1b1b;
    --ink-soft: #2a2a2a;
    --paper: #ffffff;
    --photo-light: #e9e9e9;
    --photo-dark: #3d3d3d;
  }
  * { margin: 0; padding: 0; box-sizing: border-box; }
  html, body {
    width: 1200px;
    height: 897px;
    overflow: hidden;
    background: var(--backdrop);
  }
  .stage {
    position: relative;
    width: 1200px;
    height: 897px;
  }
  .card {
    position: absolute;
    left: 329px;
    width: 543px;
    height: 310px;
    overflow: hidden;
  }
  .card--front { top: 108px; background: var(--card-white); }
  .card--back  { top: 479px; background: var(--card-black); }

  .wordmark {
    position: absolute;
    left: 24px;
    top: 30px;
    font-family: "Roboto", sans-serif;
    font-weight: 400;
    font-size: 30px;
    line-height: 1;
    color: var(--ink);
    letter-spacing: 0.2px;
  }

  .portrait {
    position: absolute;
    left: 26px;
    top: 82px;
    width: 177px;
    height: 228px;
    background: radial-gradient(ellipse at 50% 30%, var(--photo-light) 0%, #9a9a9a 45%, var(--photo-dark) 100%);
    border-radius: 80px 80px 0 0;
  }

  .contact {
    position: absolute;
    left: 289px;
    top: 118px;
    font-family: "Work Sans", sans-serif;
    color: var(--ink-soft);
    font-size: 14px;
    line-height: 22px;
  }
  .contact__name {
    font-family: "Roboto", sans-serif;
    font-weight: 500;
    font-size: 17px;
    letter-spacing: 1.6px;
    color: var(--ink);
    line-height: 22px;
  }
  .contact__role { margin-bottom: 11px; }
  .contact__address { margin-bottom: 12px; }
  .contact__row { display: flex; }
  .contact__label { width: 50px; }
  .contact__sep { width: 15px; }

  .back-lockup {
    position: absolute;
    left: 0;
    right: 0;
    top: 118px;
    display: flex;
    flex-direction: column;
    align-items: center;
    gap: 18px;
  }
  .back-lockup__square {
    width: 40px;
    height: 40px;
    background: var(--paper);
  }
  .back-lockup__name {
    font-family: "Roboto", sans-serif;
    font-weight: 400;
    font-size: 32px;
    line-height: 1;
    color: var(--paper);
  }
</style>
</head>
<body>
<main class="stage">
  <section class="card card--front" aria-label="Card front">
    <div class="wordmark">TOBIAS LENDHART</div>
    <div class="portrait" role="img" aria-label="Black and white portrait photo of the trainer, arms crossed"></div>
    <div class="contact">
      <div class="contact__name">TOBIAS LENDHART</div>
      <div class="contact__role">Personal Trainer</div>
      <div class="contact__address">Wiesengrundweg 14<br>80417 München</div>
      <div class="contact__row"><span class="contact__label">Phone</span><span class="contact__sep">:</span><span>0162/3819204</span></div>
      <div class="contact__row"><span class="contact__label">Email</span><span class="contact__sep">:</span><span>t.lendhart@mailpost.de</span></div>
      <div class="contact__row"><span class="contact__label">Web</span><span class="contact__sep">:</span><span>www.tobiaslendhart.de</span></div>
    </div>
  </section>

  <section class="card card--back" aria-label="Card back">
    <div class="back-lockup">
      <div class="back-lockup__square"></div>
      <div class="back-lockup__name">TOBIAS LENDHART</div>
    </div>
  </section>
</main>
</body>
</html>
```